Retail Sign for Houseplant Campaign

Sign will measure 3 to 4 foot tall by 22.2inches and place on rolling racks of houseplants for a retail promotion in The Birchwell Yard. The theme of the promotion will be "New Year, New You!" Selling points which should be on the sign are Houseplants give you a taste of nature, Houseplants boost air quality inside your home, Indoor plants reduce anxiety, Indoor plants make you more productive, Houseplants improve your concentration and memory.
Updates

Target Market(s)

People who love plants

Industry/Entity Type

Horticulture/ retail

Colors
00AB8E
00BBA5
67D7C9
C6EFE9
E9F9F6
59FF00
82FF00
B8FF75
E3FFCB
F4FFEA
FFF300
FFF600
FEFA6F
FFFEC7
FFFEE8

Requirements
Must have
• Must feel energetic and encourage people to buy plants. Should include 1-2 photos and the selling points listed

```html
<!DOCTYPE html>
<html lang="en">
<head>
<meta charset="utf-8">
<title>New Year New You – Houseplant Sign</title>
<link rel="stylesheet" href="https://fonts.googleapis.com/css2?family=Montserrat:wght@400&family=Righteous&display=swap">
<style>
  :root {
    --mat: #3b3b3d;
    --paper: #ffffff;
    --green-deep: #2f7f3b;
    --green-light: #8cc85a;
    --shade: #b5b6b9;
    --ink: #2a2a2a;
  }
  html, body {
    margin: 0;
    padding: 0;
    width: 822px;
    height: 1200px;
    overflow: hidden;
    background: var(--mat);
  }
  .canvas {
    width: 822px;
    height: 1200px;
    background: var(--mat);
  }
  .sign {
    display: block;
    width: 822px;
    height: 1200px;
  }
  .headline {
    font-family: "Righteous", "Arial Rounded MT Bold", sans-serif;
    font-size: 160px;
  }
  .headline-extrude { fill: var(--green-deep); }
  .headline-face {
    fill: var(--paper);
    stroke: var(--green-light);
    stroke-width: 8px;
    paint-order: stroke;
    stroke-linejoin: round;
  }
  .selling-point {
    font-family: "Montserrat", Arial, sans-serif;
    font-size: 29px;
    font-weight: 400;
    fill: var(--ink);
    letter-spacing: 0.5px;
  }
  .photo-frame {
    fill: var(--paper);
    stroke: var(--paper);
    stroke-width: 26;
    stroke-linejoin: round;
  }
</style>
</head>
<body>
<div class="canvas">
  <svg class="sign" viewBox="0 0 1591 2323" xmlns="http://www.w3.org/2000/svg">
    <defs>
      <clipPath id="board">
        <rect x="204" y="204" width="1183" height="1915"/>
      </clipPath>
      <filter id="softShadow" x="-30%" y="-30%" width="160%" height="160%">
        <feGaussianBlur stdDeviation="45"/>
      </filter>
      <linearGradient id="topBand" x1="0" y1="0.3" x2="1" y2="0">
        <stop offset="0" stop-color="#6fb64c"/>
        <stop offset="0.5" stop-color="#a8cf62"/>
        <stop offset="0.7" stop-color="#5aa54c"/>
        <stop offset="1" stop-color="#4f9a48"/>
      </linearGradient>
      <linearGradient id="bottomBand" x1="0" y1="1" x2="1" y2="0.6">
        <stop offset="0" stop-color="#b3d56a"/>
        <stop offset="0.45" stop-color="#5fb255"/>
        <stop offset="1" stop-color="#34a85a"/>
      </linearGradient>
      <linearGradient id="leftBand" x1="0" y1="0" x2="0" y2="1">
        <stop offset="0" stop-color="#3a8440"/>
        <stop offset="1" stop-color="#3a8440" stop-opacity="0"/>
      </linearGradient>
      <radialGradient id="centreShade" cx="0.5" cy="0.5" r="0.5">
        <stop offset="0" stop-color="#b8b9bc"/>
        <stop offset="1" stop-color="#ffffff" stop-opacity="0"/>
      </radialGradient>
      <linearGradient id="mainPhoto" x1="0" y1="0" x2="1" y2="0">
        <stop offset="0" stop-color="#3a2f28"/>
        <stop offset="0.3" stop-color="#d9c2b4"/>
        <stop offset="0.6" stop-color="#f1f1ef"/>
        <stop offset="0.85" stop-color="#4d8a45"/>
        <stop offset="1" stop-color="#2f6a2e"/>
      </linearGradient>
      <linearGradient id="circlePhoto" x1="0" y1="0" x2="1" y2="1">
        <stop offset="0" stop-color="#9a7d66"/>
        <stop offset="0.5" stop-color="#3a4c6e"/>
        <stop offset="1" stop-color="#5a7a5c"/>
      </linearGradient>
      <linearGradient id="leafIcon" x1="0" y1="1" x2="1" y2="0">
        <stop offset="0" stop-color="#2f8f3a"/>
        <stop offset="1" stop-color="#8fd05a"/>
      </linearGradient>
    </defs>

    <g clip-path="url(#board)">
      <!-- sign board -->
      <rect x="204" y="204" width="1183" height="1915" fill="var(--paper)"/>

      <!-- soft shading -->
      <path d="M244 885 C460 730 800 600 1205 532 C1215 800 1130 1040 940 1190 C760 1320 520 1365 244 1370 Z" fill="var(--shade)" filter="url(#softShadow)" opacity="0.9"/>
      <ellipse cx="700" cy="1480" rx="420" ry="230" fill="url(#centreShade)"/>

      <!-- top green band -->
      <path d="M204 204 L1105 204 C1118 225 1124 250 1122 268 C1080 380 1000 460 900 515 L204 885 Z" fill="url(#topBand)"/>

      <!-- bottom green band -->
      <path d="M204 1345 L412 1345 C388 1450 386 1580 395 1700 L480 1990 C700 2012 1100 1960 1387 1750 L1387 2119 L204 2119 Z" fill="url(#bottomBand)"/>
      <path d="M204 1345 L345 1345 C265 1460 218 1660 204 1880 Z" fill="url(#leftBand)"/>

      <!-- main photo -->
      <path class="photo-frame" d="M204 845 C420 690 760 560 1165 492 C1175 760 1090 1000 900 1150 C720 1280 480 1325 204 1330 Z"/>
      <path d="M204 845 C420 690 760 560 1165 492 C1175 760 1090 1000 900 1150 C720 1280 480 1325 204 1330 Z" fill="url(#mainPhoto)" role="img" aria-label="Photo of a smiling woman wiping the leaves of a monstera houseplant"/>

      <!-- circle photo -->
      <circle cx="488" cy="1838" r="213" fill="var(--paper)"/>
      <circle cx="488" cy="1838" r="201" fill="url(#circlePhoto)" role="img" aria-label="Photo of a mother and daughter watering a snake plant"/>
    </g>

    <!-- headline -->
    <g class="headline">
      <text class="headline-extrude" x="299" y="422" textLength="720" lengthAdjust="spacingAndGlyphs">NEW YEAR</text>
      <text class="headline-extrude" x="299" y="544" textLength="732" lengthAdjust="spacingAndGlyphs">NEW YOU!</text>
      <text class="headline-face" x="285" y="408" textLength="720" lengthAdjust="spacingAndGlyphs">NEW YEAR</text>
      <text class="headline-face" x="285" y="530" textLength="732" lengthAdjust="spacingAndGlyphs">NEW YOU!</text>
    </g>

    <!-- selling points -->
    <g class="selling-points">
      <path transform="translate(776 1380)" d="M0 50 C0 20 20 4 46 0 C44 30 28 48 0 50 Z" fill="url(#leafIcon)"/>
      <text class="selling-point" x="846" y="1400">Houseplants give you a</text>
      <text class="selling-point" x="846" y="1436">taste of nature.</text>

      <path transform="translate(776 1472)" d="M0 50 C0 20 20 4 46 0 C44 30 28 48 0 50 Z" fill="url(#leafIcon)"/>
      <text class="selling-point" x="846" y="1493">Houseplants boost air</text>
      <text class="selling-point" x="846" y="1530">quality inside your home.</text>

      <path transform="translate(776 1566)" d="M0 50 C0 20 20 4 46 0 C44 30 28 48 0 50 Z" fill="url(#leafIcon)"/>
      <text class="selling-point" x="846" y="1587">Indoor plants reduce</text>
      <text class="selling-point" x="846" y="1624">anxiety.</text>

      <path transform="translate(776 1660)" d="M0 50 C0 20 20 4 46 0 C44 30 28 48 0 50 Z" fill="url(#leafIcon)"/>
      <text class="selling-point" x="846" y="1681">Indoor plants make you</text>
      <text class="selling-point" x="846" y="1718">more productive.</text>

      <path transform="translate(776 1754)" d="M0 50 C0 20 20 4 46 0 C44 30 28 48 0 50 Z" fill="url(#leafIcon)"/>
      <text class="selling-point" x="846" y="1774">Houseplants improve</text>
      <text class="selling-point" x="846" y="1811">your concentration</text>
      <text class="selling-point" x="846" y="1847">and memory.</text>
    </g>
  </svg>
</div>
</body>
</html>
```